Business card design for a dynamic IT consulting company

We need a business card design for a young firm, specialized in the Telecommunications/Consulting industry. The name of the company is Quindor and Partners Business Consulting Ltd. (Short name: Quindor and Partnes)
Quindor = solve read reverse, so we aim to be uncomplicated and solution-oriented. The small pipe in our logo is also related to the word solve. So we need a new business card design, which is simple, eye catching and something non traditional (I would probably prefer a square shaped design rather than a rectangle, but open for suggestions). Attached our logo.

Target Market(s)

Usually our customers are Tier1 Telecoms providers (Q-Netra, Palorix, etc) and their executives.

Industry/Entity Type

Business

Contact Information for Business Card

Name: Bence Tolnavari
Email: b.tolnavari@quindor.hu
Web: www.quindor.hu
Mobile: +36 30 518 2769
Title: Managing Director

Optional:
Company name: Quindor and Partners Ltd.
Address: 1087 Budapest, Tolvenka str. 28/C, Hungary

Font styles to use
Other font styles liked:
• helveticaneue_medium, Prime Regular are used now.

Colors

Designer to choose colors to be used in the design.

Requirements
Must have
• I would like to have a 2 sided design.
Nice to have
• I thought if we make the logo a bit bigger (without the company name), that could go to the back with the company name below. I though, if the pipe in the logo is somehow touchable on the business card, would be nice and unique.

```html
<!DOCTYPE html>
<html lang="en">
<head>
<meta charset="utf-8">
<title>Quindor &amp; Partners – Business Card</title>
<link rel="stylesheet" href="https://fonts.googleapis.com/css2?family=Arimo:wght@400;500&display=swap">
<style>
  :root {
    --backdrop: #1c1c1c;
    --card: #242424;
    --card-edge: #2fb3e4;
    --ink-light: #e6e6e6;
    --ink-muted: #cfcfcf;
    --accent-blue: #1d87c8;
    --accent-magenta: #a4347f;
    --divider: #1b5f8c;
  }
  * { margin: 0; padding: 0; box-sizing: border-box; }
  html, body {
    width: 1000px; height: 1200px; overflow: hidden;
    background: var(--backdrop);
    font-family: "Arimo", "Helvetica Neue", Arial, sans-serif;
  }
  .sheet {
    width: 1000px; height: 1200px;
    display: flex; flex-direction: column; align-items: center; justify-content: space-around;
    padding: 70px 0;
  }
  .card {
    position: relative;
    width: 760px; height: 434px;
    background: var(--card);
    border-left: 3px solid var(--card-edge);
    border-bottom: 3px solid var(--card-edge);
    box-shadow: 0 30px 60px rgba(0,0,0,.55);
  }

  /* Front */
  .card-front .brand-block {
    position: absolute; left: 0; top: 0; width: 52%; height: 100%;
    display: flex; align-items: center; justify-content: center; gap: 12px;
  }
  .brand-mark {
    width: 14px; height: 14px; background: var(--accent-magenta);
  }
  .brand-name {
    font-size: 34px; font-weight: 400; color: var(--ink-light); letter-spacing: .5px;
  }
  .card-front .divider {
    position: absolute; left: 52%; top: 48px; bottom: 48px;
    width: 1px; background: var(--divider);
  }
  .contact-block {
    position: absolute; left: calc(52% + 36px); top: 116px;
  }
  .person-name {
    font-size: 22px; font-weight: 400; color: var(--ink-light);
  }
  .person-title {
    font-size: 15px; color: var(--accent-blue); margin-top: 4px;
  }
  .contact-list {
    list-style: none; margin-top: 30px;
  }
  .contact-list li {
    display: flex; align-items: center; gap: 10px;
    font-size: 16px; color: var(--ink-muted); line-height: 28px;
  }
  .contact-list svg { width: 16px; height: 16px; flex: none; }

  /* Back */
  .card-back .brand-block {
    position: absolute; left: 0; right: 0; top: 110px;
    display: flex; align-items: center; justify-content: center; gap: 18px;
  }
  .card-back .brand-mark { width: 22px; height: 22px; }
  .card-back .brand-name { font-size: 52px; }
  .address {
    position: absolute; left: 150px; bottom: 74px;
    display: flex; align-items: center; gap: 10px;
    font-size: 18px; color: var(--ink-muted);
  }
  .address svg { width: 14px; height: 18px; }
</style>
</head>
<body>
<main class="sheet">

  <section class="card card-front" aria-label="Business card, front">
    <div class="brand-block">
      <span class="brand-mark"></span>
      <span class="brand-name">Quindor &amp; Partners</span>
    </div>
    <div class="divider"></div>
    <div class="contact-block">
      <p class="person-name">Bence Tolnavari</p>
      <p class="person-title">Managing Director</p>
      <ul class="contact-list">
        <li>
          <svg viewBox="0 0 16 16" fill="none" stroke="#1d87c8" stroke-width="1.3"><rect x="4" y="1" width="8" height="14" rx="1.5"/><line x1="7" y1="12.5" x2="9" y2="12.5"/></svg>
          +36 30 518 2769
        </li>
        <li>
          <svg viewBox="0 0 16 16" fill="none" stroke="#1d87c8" stroke-width="1.3"><rect x="1.5" y="3.5" width="13" height="9"/><polyline points="1.5,3.5 8,9 14.5,3.5"/></svg>
          b.tolnavari@quindor.hu
        </li>
        <li>
          <svg viewBox="0 0 16 16" fill="none" stroke="#1d87c8" stroke-width="1.2"><circle cx="8" cy="8" r="6.5"/><ellipse cx="8" cy="8" rx="2.8" ry="6.5"/><line x1="1.5" y1="8" x2="14.5" y2="8"/></svg>
          www.quindor.hu
        </li>
      </ul>
    </div>
  </section>

  <section class="card card-back" aria-label="Business card, back">
    <div class="brand-block">
      <span class="brand-mark"></span>
      <span class="brand-name">Quindor &amp; Partners</span>
    </div>
    <p class="address">
      <svg viewBox="0 0 14 18" fill="none" stroke="#1d87c8" stroke-width="1.6"><path d="M7 17 C3 11 1.5 8.5 1.5 6.5 A5.5 5.5 0 0 1 12.5 6.5 C12.5 8.5 11 11 7 17 Z"/><circle cx="7" cy="6.5" r="2"/></svg>
      1087 Budapest, Tolvenka str. 28/C, Hungary
    </p>
  </section>

</main>
</body>
</html>
```